Valdo Capital

We need a corporate style website design for a new company based in Shenzhen's Qianhai Special Economic Development Zone, China. We provide a range of financial services to large international investment companies. Typically these companies invest over 5 million RMB. The company is part of a group that consists of NorthKilns, ValdoTrusts and ValdoEquity. Our location and gateway into Qianhai Special Economic Zone is our core advantage. We would like to see designs that Do Not use purple and orange. The website design should be similar to other websites in this family but different enough to give it a unique style (See attached website links for reference). The final design should communicate financial safety and growth. This website will act partly as a business chamber with connections to the government so we would like it to be diplomatic in style.

www.northkilns.example
www.valdotrusts.example

*Nevegation Bar
Should including Homepage, Financial Product, Team, News.
Could refer to www.valdotrusts.example

*Contact Details

Miss Lan
Address:E 728, North Block, KMO Centre, East Sector, Shenzhen Bright Science Campus
Telephone: +86 0755 63920417
Cellphone: +86 13957280316

* Social Media
Should be grouped like:
1. Weibo QRcode+ Weibo
2. Facebook, Twitter, Linkedin.

Industry/Entity Type

Investment

```html
<!DOCTYPE html>
<html lang="en">
<head>
<meta charset="utf-8">
<title>Valdo Capital</title>
<link href="https://fonts.googleapis.com/css2?family=Cinzel:wght@600&family=Open+Sans:wght@400;600;700&display=swap" rel="stylesheet">
<style>
:root{
  --brand:#1f6fb5;
  --brand-dark:#165a94;
  --ink:#333333;
  --muted:#777777;
  --line:#e2e2e2;
  --date:#c0392b;
  --hero-top:#2c5d8f;
  --hero-bottom:#9fbcd6;
  --thumb-a:#7d93aa;
  --thumb-b:#c7d3df;
  --footer:#2a2c30;
  --footer-text:#b8bcc2;
  --page:#ffffff;
}
*{box-sizing:border-box;margin:0;padding:0}
html,body{width:874px;height:1200px;overflow:hidden}
body{background:var(--page);font-family:"Open Sans",Arial,sans-serif;color:var(--ink);position:relative}

/* Header */
.site-header{position:absolute;top:0;left:0;width:874px;height:80px;display:flex;align-items:center;padding:0 40px 0 30px;border-bottom:1px solid var(--line)}
.brand{display:flex;align-items:center;gap:10px}
.brand-mark{width:36px;height:36px;border-radius:50%;background:var(--brand)}
.brand-name{font-family:"Cinzel",Georgia,serif;font-weight:600;font-size:21px;color:var(--brand-dark);letter-spacing:1px;line-height:1}
.brand-sub{font-size:7px;color:var(--muted);margin-top:4px;letter-spacing:.3px}
.main-nav{display:flex;gap:26px;margin-left:auto;margin-right:22px;font-size:11px;color:#555}
.main-nav a{color:inherit;text-decoration:none}
.main-nav a.active{color:var(--brand)}
.search{display:flex;align-items:center}
.search-field{width:110px;height:22px;border:1px solid #ccc;border-right:none}
.search-btn{width:24px;height:22px;background:var(--brand);display:flex;align-items:center;justify-content:center}

/* Hero */
.hero{position:absolute;top:80px;left:0;width:874px;height:425px;background:linear-gradient(180deg,var(--hero-top) 0%,#4f7fae 55%,var(--hero-bottom) 100%)}
.hero-card{position:absolute;top:55px;left:597px;width:205px;height:250px;background:rgba(255,255,255,.95);padding:22px 18px;text-align:center}
.hero-card h2{font-size:15px;font-weight:700;color:var(--ink);line-height:1.3;letter-spacing:.5px;text-transform:uppercase}
.hero-card p{font-size:8px;color:var(--muted);line-height:1.55;margin-top:12px}
.btn{display:inline-block;margin-top:16px;background:var(--brand);color:#fff;font-size:9px;font-weight:600;padding:7px 16px;letter-spacing:.5px}
.slider-dots{position:absolute;top:514px;left:0;width:874px;display:flex;justify-content:center;gap:6px}
.slider-dots span{width:7px;height:7px;border-radius:50%;background:#ccc}
.slider-dots span.on{background:var(--brand)}

/* Sections */
.section-title{font-size:14px;font-weight:700;color:var(--ink)}
.about{position:absolute;top:560px;left:73px;width:380px}
.about .section-title{border-bottom:1px solid var(--line);padding-bottom:8px;margin-bottom:14px}
.about-row{display:flex;gap:12px}
.about-img{flex:0 0 104px;height:92px;background:linear-gradient(135deg,var(--thumb-a),var(--thumb-b))}
.about p{font-size:8px;line-height:1.6;color:var(--muted)}
.about p.more{margin-top:8px}

.news{position:absolute;top:560px;left:562px;width:238px}
.news-head{display:flex;justify-content:space-between;align-items:baseline;border-bottom:1px solid var(--line);padding-bottom:8px;margin-bottom:10px}
.news-head a{font-size:9px;color:var(--muted);text-decoration:none}
.news-item{display:flex;gap:10px;margin-bottom:14px}
.news-thumb{flex:0 0 70px;height:56px;background:linear-gradient(135deg,var(--thumb-a),var(--thumb-b))}
.news-item h3{font-size:10px;font-weight:600;color:var(--ink)}
.news-item p{font-size:7.5px;color:var(--muted);line-height:1.5;margin-top:2px}
.news-item .date{font-size:7.5px;color:var(--date);margin-top:3px}

.blog{position:absolute;top:860px;left:73px;width:727px}
.divider-title{display:flex;align-items:center;gap:14px;justify-content:center}
.divider-title::before,.divider-title::after{content:"";flex:1;height:1px;background:var(--line)}
.blog-grid{display:flex;gap:0;margin-top:20px;padding-left:43px}
.post{display:flex;gap:12px;width:335px}
.post-img{flex:0 0 102px;height:96px;background:linear-gradient(135deg,#5f7892,#b9c7d5)}
.post h3{font-size:11px;font-weight:700;color:var(--ink)}
.post p{font-size:7.5px;line-height:1.6;color:var(--muted);margin-top:6px}
.post-meta{display:flex;justify-content:space-between;font-size:7.5px;margin-top:8px;width:190px}
.post-meta a{color:var(--brand);text-decoration:none}
.post-meta span{color:var(--muted)}

.clients{position:absolute;top:1040px;left:73px;width:727px;text-align:center}
.clients h2{font-size:12px;font-weight:600;color:var(--ink)}
.client-row{display:flex;justify-content:space-between;margin-top:14px;padding:0 20px}
.client{width:96px;height:60px;border:1px solid var(--line);display:flex;flex-direction:column;align-items:center;justify-content:center;gap:5px;font-size:8px;font-weight:600;color:#555}
.client i{width:18px;height:18px;border-radius:50%;background:#9aa9b8;display:block}

/* Footer */
.site-footer{position:absolute;top:1150px;left:0;width:874px;height:50px;background:var(--footer);padding:10px 73px;display:flex;justify-content:space-between;align-items:center}
.footer-links{display:flex;gap:14px;font-size:8px;color:#e6e6e6}
.copyright{font-size:7px;color:var(--footer-text);margin-top:5px}
.social{display:flex;gap:7px}
.social span{width:14px;height:14px;background:#5b5f66;display:block}
</style>
</head>
<body>

<header class="site-header">
  <div class="brand">
    <span class="brand-mark"></span>
    <div>
      <div class="brand-name">Valdo Capital</div>
      <div class="brand-sub">Valdo Capital Investment Advisory Co., Ltd.</div>
    </div>
  </div>
  <nav class="main-nav">
    <a class="active" href="#">Home</a>
    <a href="#">Financial Product</a>
    <a href="#">Team</a>
    <a href="#">News</a>
  </nav>
  <div class="search">
    <span class="search-field"></span>
    <span class="search-btn">
      <svg width="11" height="11" viewBox="0 0 12 12"><circle cx="5" cy="5" r="3.6" fill="none" stroke="#fff" stroke-width="1.5"/><line x1="7.7" y1="7.7" x2="11" y2="11" stroke="#fff" stroke-width="1.5"/></svg>
    </span>
  </div>
</header>

<section class="hero" role="img" aria-label="Glass office towers of a financial district under a blue sky">
  <div class="hero-card">
    <h2>Lorem ipsum dolor<br>sit amet</h2>
    <p>Long established fact that a reader will be distracted by the readable content of a page when looking at its layout. The point of using Lorem Ipsum is that it has a more normal distribution.</p>
    <span class="btn">READ MORE</span>
  </div>
</section>
<div class="slider-dots"><span class="on"></span><span></span><span></span></div>

<section class="about">
  <h2 class="section-title">About Us</h2>
  <div class="about-row">
    <div class="about-img" role="img" aria-label="Business team meeting in an office"></div>
    <p>Contrary to popular belief, Lorem Ipsum is not simply random text. It has roots in a piece of classical Latin literature from 45 BC, making it over 2000 years old. A Latin professor looked up one of the more obscure Latin words, consectetur, and going through the cites of the word in classical literature, discovered the undoubtable source.</p>
  </div>
  <p class="more">Lorem Ipsum comes from sections of a classical text on the theory of ethics, very popular during the Renaissance. The first line of Lorem Ipsum comes from a line in section 1.10.32.</p>
</section>

<section class="news">
  <div class="news-head"><h2 class="section-title">News and Events</h2><a href="#">Read More</a></div>
  <article class="news-item">
    <div class="news-thumb" role="img" aria-label="Business meeting news photo"></div>
    <div><h3>Lorem ipsum dolor</h3><p>Lorem ipsum dolor sit amet, consectetur adipiscing elit sed do.</p><div class="date">Oct 30, 2014 8:46 pm</div></div>
  </article>
  <article class="news-item">
    <div class="news-thumb" role="img" aria-label="City skyline news photo"></div>
    <div><h3>Lorem ipsum dolor</h3><p>Lorem ipsum dolor sit amet, consectetur adipiscing elit sed do.</p><div class="date">Oct 30, 2014 8:46 pm</div></div>
  </article>
  <article class="news-item">
    <div class="news-thumb" role="img" aria-label="Conference event news photo"></div>
    <div><h3>Lorem ipsum dolor</h3><p>Lorem ipsum dolor sit amet, consectetur adipiscing elit sed do.</p><div class="date">Oct 30, 2014 8:46 pm</div></div>
  </article>
</section>

<section class="blog">
  <h2 class="section-title divider-title">From the Blog</h2>
  <div class="blog-grid">
    <article class="post">
      <div class="post-img" role="img" aria-label="Business handshake blog photo"></div>
      <div>
        <h3>Adipiscing Mollis Inceptos</h3>
        <p>Aenean leo quam, pellentesque ornare sem lacinia quam venenatis vestibulum. Maecenas sed diam eget risus varius blandit.</p>
        <div class="post-meta"><a href="#">Continue Reading »</a><span>26 Jan 2014</span></div>
      </div>
    </article>
    <article class="post">
      <div class="post-img" role="img" aria-label="Office desk with documents blog photo"></div>
      <div>
        <h3>Inceptos Purus Amet Consectetur</h3>
        <p>Aenean leo quam, pellentesque ornare sem lacinia quam venenatis vestibulum. Maecenas sed diam eget risus varius blandit.</p>
        <div class="post-meta"><a href="#">Continue Reading »</a><span>26 Jan 2014</span></div>
      </div>
    </article>
  </div>
</section>

<section class="clients">
  <h2>Some of our Clients who love being with us!</h2>
  <div class="client-row">
    <div class="client"><i></i>Harbor Lane</div>
    <div class="client"><i></i>Brightpath</div>
    <div class="client"><i></i>Kestrel Group</div>
    <div class="client"><i></i>Oakmere</div>
    <div class="client"><i></i>Lumen Trade</div>
    <div class="client"><i></i>Sable &amp; Co</div>
  </div>
</section>

<footer class="site-footer">
  <div>
    <div class="footer-links"><span>Contact Us</span><span>Privacy &amp; Security</span><span>Terms of Use</span><span>Opt-out</span></div>
    <div class="copyright">Copyright 2014 valdocapital.example All Rights Reserved</div>
  </div>
  <div class="social"><span></span><span></span><span></span><span></span><span></span></div>
</footer>

</body>
</html>
```